Business Cards Design for the electrical wholesaler: clean bold dynamic :)

We need a business card design that would follow our latest brand guidelines. As an electrical wholesaler we want to bring a fresh look and feel into the industry. The design should be clean bold and dynamic. It should come alive with the renewed energy of our green colour. Our grey colour should keep things balanced and complement the notion of maturity and responsibility. We employ Lato as a corporate font however are not bound by this font and we’re open to interpretation here.

Target Market(s)

Electrical contractors

Industry/Entity Type

Business

Contact Information for Business Card

Logo
Name & Surname: Halyna Dorosh
Job Title: Director of Marketing
Email: halya.dorosh@quillmail.example
Cell phone: XXX.XXX.XXXX
Address: 20517 - 87 Ave. Edmonton, AB, Canada. T6K 4N8
Business Phone: 780.555.0184
Website: www.brovix.example

Font styles to use
Other font styles liked:
• Lato

Requirements
Must have
• Logo & website
Nice to have
• Brand elements - some of them you may find in the attached Brand Guidelines (e.g. three lines on the background signifying "W")

```html
<!DOCTYPE html>
<html lang="en">
<head>
<meta charset="utf-8">
<title>Brovix business cards</title>
<link rel="stylesheet" href="https://fonts.googleapis.com/css2?family=Work+Sans:wght@400;500;600&display=swap">
<style>
  :root {
    --backdrop: #4a403b;
    --card: #1c1d1e;
    --card-deep: #151617;
    --gloss: #0b0b0c;
    --silver: #c9cbcc;
    --silver-soft: #a7aaac;
    --green: #6fbf2a;
    --rule: #6d7072;
  }
  * { box-sizing: border-box; margin: 0; padding: 0; }
  html, body { width: 1200px; height: 715px; overflow: hidden; }
  body {
    background: var(--backdrop);
    font-family: "Work Sans", Arial, sans-serif;
    display: flex;
    align-items: center;
    justify-content: center;
    gap: 56px;
  }
  .card {
    width: 520px;
    height: 297px;
    background: linear-gradient(160deg, var(--card), var(--card-deep));
    position: relative;
    display: flex;
    align-items: center;
  }
  .card--front {
    justify-content: center;
    box-shadow: 0 0 0 3px var(--green);
  }
  .brand {
    display: flex;
    flex-direction: column;
    align-items: flex-end;
  }
  .brand__name {
    font-weight: 500;
    line-height: 0.9;
    letter-spacing: -1px;
  }
  .brand__tagline {
    font-size: 8px;
    letter-spacing: 2.6px;
    text-transform: uppercase;
    margin-top: 4px;
  }
  .card--front .brand__name { font-size: 96px; color: var(--gloss); }
  .card--front .brand__tagline { font-size: 11px; letter-spacing: 3.4px; color: var(--silver-soft); }
  .card--back { padding: 0 36px 0 40px; }
  .card--back .brand__name { font-size: 60px; color: var(--silver); }
  .card--back .brand__tagline { color: var(--gloss); font-weight: 600; }
  .divider {
    width: 1px;
    height: 150px;
    background: var(--rule);
    margin: 0 24px;
  }
  .contact { color: var(--silver); font-size: 12.5px; line-height: 1.45; }
  .contact__name { font-size: 20px; font-weight: 600; line-height: 1.1; }
  .contact__title { color: var(--silver-soft); margin-bottom: 6px; }
  .contact__row { display: flex; align-items: center; gap: 7px; }
  .contact__row svg { width: 9px; height: 9px; flex: none; }
  .contact__row--plain { padding-left: 16px; }
</style>
</head>
<body>
  <section class="card card--front" aria-label="Card front">
    <div class="brand">
      <span class="brand__name">brovix</span>
      <span class="brand__tagline">Electrical Wholesalers</span>
    </div>
  </section>

  <section class="card card--back" aria-label="Card back">
    <div class="brand">
      <span class="brand__name">brovix</span>
      <span class="brand__tagline">Electrical Wholesalers</span>
    </div>
    <div class="divider"></div>
    <div class="contact">
      <p class="contact__name">Halyna Dorosh</p>
      <p class="contact__title">Founder</p>
      <p class="contact__row contact__row--plain">20517 87ave</p>
      <p class="contact__row contact__row--plain">T6K4N8 Edmonton, Alberta</p>
      <p class="contact__row">
        <svg viewBox="0 0 10 10" aria-hidden="true"><path d="M2 1l2 2-1 1.2c.6 1.2 1.5 2.1 2.8 2.8L7 6l2 2-1.3 1.3C4.5 9 1 5.5.7 2.3z" fill="var(--silver)"/></svg>
        780.555.0184
      </p>
      <p class="contact__row">
        <svg viewBox="0 0 10 10" aria-hidden="true"><rect x="0.8" y="2" width="8.4" height="6" fill="none" stroke="var(--silver)" stroke-width="1"/><path d="M1 2.3l4 3 4-3" fill="none" stroke="var(--silver)" stroke-width="1"/></svg>
        halya.dorosh@quillmail.example
      </p>
      <p class="contact__row">
        <svg viewBox="0 0 10 10" aria-hidden="true"><circle cx="5" cy="5" r="4.2" fill="none" stroke="var(--silver)" stroke-width="1"/><ellipse cx="5" cy="5" rx="1.8" ry="4.2" fill="none" stroke="var(--silver)" stroke-width="0.8"/><path d="M.8 5h8.4" stroke="var(--silver)" stroke-width="0.8"/></svg>
        www.brovix.example
      </p>
    </div>
  </section>
</body>
</html>
```